Home Remodeling company needs a business card design

we need a business card design for home remodeling company in hamilton county, indiana USA. we offers a wide range of construction services including whole house renovations, Design and Build Basements and Kitchen and Bathroom Remodeling . we would like to see designs for both site of business card that use the same color of the company logo and also including all information below :
1- Karim Feltous CEO / General Contractor
2- all company contacts Telephone numbers ( 1-888-DULOM-47 ) ( 317-555-0193) email address ( info@dulomhome.com) website ( www.dulomhome.com ) and social media logos (Facebook- twitter- google plus )
3- company logo
4- licensed . insured . bonded

```html
<!DOCTYPE html>
<html lang="en">
<head>
<meta charset="utf-8">
<title>Dulom Home Remodeling – Business Card</title>
<link rel="stylesheet" href="https://fonts.googleapis.com/css2?family=Montserrat:wght@400;800&family=Arimo:wght@400&family=Tinos&display=swap">
<style>
  :root {
    --backdrop: #2f2925;
    --card: #1c1c1d;
    --card-edge: #101011;
    --white: #f4f4f4;
    --grey: #a9a9a9;
    --rule: #8a8a8a;
    --red: #c8222c;
    --chip: #3a3a3c;
  }
  * { margin: 0; padding: 0; box-sizing: border-box; }
  html, body { width: 1200px; height: 780px; overflow: hidden; }
  body {
    background: var(--backdrop);
    position: relative;
    font-family: "Arimo", Arial, sans-serif;
    color: var(--white);
  }
  .card {
    position: absolute;
    top: 236px;
    width: 540px;
    height: 308px;
    background: var(--card);
    border: 1px solid var(--card-edge);
    box-shadow: 0 10px 28px rgba(0,0,0,.45);
  }
  .card--front { left: 40px; }
  .card--back { left: 620px; }

  .brand { position: absolute; display: flex; flex-direction: column; }
  .brand__row { display: flex; align-items: center; gap: 10px; }
  .brand__mark { width: 14px; height: 14px; background: var(--red); }
  .brand__name {
    font-family: "Montserrat", Arial, sans-serif;
    font-weight: 800;
    color: var(--white);
    letter-spacing: 1px;
    line-height: 1;
  }
  .brand__tagline {
    font-family: "Montserrat", Arial, sans-serif;
    font-weight: 400;
    color: var(--grey);
    text-transform: uppercase;
  }

  .card--front .brand { left: 30px; top: 24px; }
  .card--front .brand__name { font-size: 44px; }
  .card--front .brand__tagline { font-size: 12px; letter-spacing: 6px; margin: 4px 0 0 24px; }

  .credentials { position: absolute; left: 30px; top: 104px; font-size: 14px; color: var(--white); }
  .divider { position: absolute; left: 30px; right: 30px; top: 128px; height: 1px; background: var(--rule); }

  .contacts { position: absolute; left: 30px; top: 150px; list-style: none; }
  .contacts li { display: flex; align-items: center; gap: 10px; font-size: 15px; line-height: 22px; }
  .contacts svg { width: 13px; height: 13px; flex: none; }

  .person { position: absolute; right: 30px; top: 150px; text-align: right; }
  .person__name { font-family: "Tinos", "Times New Roman", serif; font-size: 27px; color: var(--red); }
  .person__role { font-size: 15px; color: var(--white); margin-top: 2px; }

  .social { position: absolute; right: 30px; bottom: 28px; display: flex; gap: 10px; list-style: none; }
  .social li { width: 36px; height: 36px; border-radius: 5px; background: var(--chip); }

  .card--back .brand { left: 50%; top: 50%; transform: translate(-50%, -50%); }
  .card--back .brand__name { font-size: 62px; }
  .card--back .brand__mark { width: 18px; height: 18px; }
  .card--back .brand__tagline { font-size: 15px; letter-spacing: 9px; margin: 6px 0 0 28px; }
</style>
</head>
<body>
  <section class="card card--front" aria-label="Card front">
    <div class="brand">
      <div class="brand__row"><span class="brand__mark"></span><span class="brand__name">DULOM</span></div>
      <span class="brand__tagline">Home Remodeling</span>
    </div>
    <p class="credentials">licensed . insured . bonded</p>
    <div class="divider"></div>

    <ul class="contacts">
      <li><svg viewBox="0 0 14 14"><rect width="14" height="14" rx="2" fill="#c8222c"/><path d="M4 3l2 0 .6 2.2-1 .8a6 6 0 0 0 2.4 2.4l.8-1L11 8v2c-4 .4-7.4-3-7-7z" fill="#fff"/></svg>317-555-0193</li>
      <li><svg viewBox="0 0 14 14"><rect width="14" height="14" rx="2" fill="#c8222c"/><path d="M4 3l2 0 .6 2.2-1 .8a6 6 0 0 0 2.4 2.4l.8-1L11 8v2c-4 .4-7.4-3-7-7z" fill="#fff"/></svg>1-888-DULOM-47</li>
      <li><svg viewBox="0 0 14 14"><rect width="14" height="14" rx="2" fill="#c8222c"/><circle cx="7" cy="7" r="4" fill="none" stroke="#fff" stroke-width="1.2"/><path d="M3 7h8M7 3c-2 2.5-2 5.5 0 8M7 3c2 2.5 2 5.5 0 8" fill="none" stroke="#fff" stroke-width="1"/></svg>www.dulomhome.com</li>
      <li><svg viewBox="0 0 14 14"><rect width="14" height="14" rx="2" fill="#c8222c"/><rect x="3" y="4" width="8" height="6" fill="none" stroke="#fff" stroke-width="1.2"/><path d="M3 4l4 3.5L11 4" fill="none" stroke="#fff" stroke-width="1.2"/></svg>info@dulomhome.com</li>
    </ul>

    <div class="person">
      <p class="person__name">Karim Feltous</p>
      <p class="person__role">CEO / General Contractor</p>
    </div>

    <ul class="social" aria-label="Social media">
      <li></li><li></li><li></li>
    </ul>
  </section>

  <section class="card card--back" aria-label="Card back">
    <div class="brand">
      <div class="brand__row"><span class="brand__mark"></span><span class="brand__name">DULOM</span></div>
      <span class="brand__tagline">Home Remodeling</span>
    </div>
  </section>
</body>
</html>
```